furniture and home contents restoration

I need to list the services that we perform in our studio.
we serve the general public as well as the insurance/ remediation industry

```html
<!DOCTYPE html>
<html lang="en">
<head>
<meta charset="utf-8">
<title>Paramount Restorers – Business Card</title>
<link href="https://fonts.googleapis.com/css2?family=Noto+Serif:wght@400;700&display=swap" rel="stylesheet">
<style>
:root{
  --backdrop:#d6d6d6;
  --card:#21303a;
  --ink:#ffffff;
}
*{margin:0;padding:0;box-sizing:border-box}
html,body{width:1200px;height:965px;overflow:hidden;background:var(--backdrop)}
body{position:relative;font-family:"Noto Serif",serif;color:var(--ink)}
.card{position:absolute;top:159px;width:383px;height:668px;background:var(--card);overflow:hidden}
.card--front{left:186px}
.card--back{left:653px}
.brand{position:absolute;left:0;right:0;text-align:center;font-weight:700;line-height:1.18;letter-spacing:.5px}
.card--front .brand{top:44px;font-size:43px}
.card--back .brand{top:22px;font-size:49px}
.holder{position:absolute;left:45px;top:318px;font-size:26px;font-weight:700}
.rule{position:absolute;left:45px;width:294px;height:2px;background:var(--ink)}
.contact{position:absolute;left:45px;list-style:none;font-size:15.5px;line-height:20px}
.contact li{display:flex;align-items:center;gap:5px;white-space:nowrap}
.contact svg{width:11px;height:11px;fill:var(--ink);flex:none}
.tagline{position:absolute;left:45px;top:557px;font-size:16.5px;line-height:22.5px}
.band{position:absolute;left:0;right:0;top:615px;height:22px}
.band__bar{position:absolute;top:4px;height:13px;background:var(--ink)}
.band__bar--left{left:0;width:32px}
.band__bar--right{right:0;width:38px}
.band__label{position:absolute;left:45px;top:0;font-size:18px;line-height:22px;white-space:nowrap}
.services{position:absolute;left:34px;list-style:none;font-size:13.6px;line-height:17.8px;white-space:nowrap}
.services li::before{content:"";display:inline-block;width:5px;height:5px;border-radius:50%;background:var(--ink);margin-right:5px;vertical-align:2px}
.services--first{top:170px}
.services--second{top:377px}
.card--back .rule{left:34px;width:313px;top:572px}
.notes{position:absolute;left:34px;top:593px;font-size:11.2px;line-height:16px;width:320px}
</style>
</head>
<body>
<section class="card card--front" aria-label="Card front">
  <h1 class="brand">PARAMOUNT<br>RESTORERS</h1>
  <h2 class="holder">DANIEL MORETTI</h2>
  <div class="rule" style="top:365px"></div>
  <ul class="contact" style="top:384px">
    <li><svg viewBox="0 0 24 24"><path d="M6.6 10.8c1.4 2.8 3.8 5.1 6.6 6.6l2.2-2.2c.3-.3.7-.4 1-.2 1.1.4 2.3.6 3.6.6.6 0 1 .4 1 1V20c0 .6-.4 1-1 1C10.6 21 3 13.4 3 4c0-.6.4-1 1-1h3.5c.6 0 1 .4 1 1 0 1.3.2 2.5.6 3.6.1.3 0 .7-.2 1z"/></svg>555 310 4200</li>
    <li><svg viewBox="0 0 24 24"><path d="M7 1h10c1.1 0 2 .9 2 2v18c0 1.1-.9 2-2 2H7c-1.1 0-2-.9-2-2V3c0-1.1.9-2 2-2zm0 3v14h10V4zm5 15.5a1.2 1.2 0 100 2.4 1.2 1.2 0 000-2.4z"/></svg>555 718 2946</li>
    <li><svg viewBox="0 0 24 24"><path d="M6 2h12v6H6zM4 9h16c1.1 0 2 .9 2 2v7h-4v4H6v-4H2v-7c0-1.1.9-2 2-2zm4 7v4h8v-4z"/></svg>555 310 4280</li>
  </ul>
  <div class="rule" style="top:463px"></div>
  <ul class="contact" style="top:483px">
    <li><svg viewBox="0 0 24 24"><path d="M2 5h20v14H2zm2 2v.5l8 5 8-5V7zm0 2.8V17h16V9.8l-8 5z"/></svg>dm4studio@example.com</li>
    <li><svg viewBox="0 0 24 24"><path d="M12 1a8 8 0 00-8 8c0 6 8 14 8 14s8-8 8-14a8 8 0 00-8-8zm0 11a3 3 0 110-6 3 3 0 010 6z"/></svg>12 birch hollow rd. riverton, ny 10599</li>
  </ul>
  <div class="rule" style="top:541px"></div>
  <p class="tagline">serving the general public and the<br>insurance industry for over 40 years</p>
  <div class="band">
    <span class="band__bar band__bar--left"></span>
    <span class="band__label">HOME CONTENTS RESTORATION</span>
    <span class="band__bar band__bar--right"></span>
  </div>
</section>

<section class="card card--back" aria-label="Card back">
  <h1 class="brand">PARAMOUNT<br>RESTORERS</h1>
  <ul class="services services--first">
    <li>ANTIQUE REPAIR AND RESTORATION</li>
    <li>ART CLEANING AND REMOUNTING</li>
    <li>ART AND MIRROR FRAME REPAIR</li>
    <li>CHANDELIER CLEANING AND RESTORATION</li>
    <li>DOCUMENT RESTORATION</li>
    <li>GLASS, CERAMIC, AND MIRROR REPAIR</li>
    <li>HARDWARE REPAIR AND RESTORATION</li>
    <li>KITCHEN REMOVAL AND REINSTALLATION</li>
    <li>LAMP CLEANING AND RESTORATION</li>
    <li>LAMP SHADE REPLACEMENT</li>
  </ul>
  <ul class="services services--second">
    <li>METAL POLISHING AND RESTORATION</li>
    <li>ODOR REMOVAL AND OZONE SERVICES</li>
    <li>PHOTO RESTORATION</li>
    <li>UPHOLSTERY CLEANING AND DEODORIZING</li>
    <li>IN-HOUSE UPHOLSTERY AND REUPHOLSTERY</li>
    <li>RUG CLEANING AND RESTORATION</li>
    <li>MUSICAL INSTRUMENT RESTORATION</li>
    <li>WINDOW TREATMENT REPAIR/ RESTORATION</li>
    <li>LEATHER RESTORATION AND REPLACEMENT</li>
    <li>PIANO RESTORATION AND REPAIR</li>
  </ul>
  <div class="rule"></div>
  <p class="notes">ON-SITE INSPECTIONS AND DESK REVIEW SERVICES<br>ASSESSMENT REPORTS AND ESTIMATES FOR REPAIR<br>AND RESTORATION</p>
</section>
</body>
</html>
```